TuneRoost - Music Industry App needs a top quality wordpress homepage

We need a modern responsive wordpress homepage built. Our website will only feature one page with the goal to get people to sign up to our app. A word document has been uploaded outlining the page content/sections.

Once the homepage is finalised, I will also need 2 landing pages built as part of this competition. It will be very similar to the homepage with the same layout etc but just feature different images and content. The homepage is for anyone (artists and venues) to find out about us but the landing pages will be artist or venue specific.

The completed work must be delivered as an exportable file into wordpress and be designed properly so no more work is needed to begin utilising as the actual website. The images used must be setup correctly for speed and quality also.

Target Market(s)

Venues and Artists.

Coding

Coded - Design and coding required

Requirements
Must have
• UPDATE: High Res Logo files attached
• Must be a modern looking website and be responsive. Must look good across all devices from desktop, to mobile and tablet. Needs to be very high quality.
• Please see the attached logo - I am waiting for the final high quality version and will reupload when complete but this will be enough to get you started for now. The website must have a dark base colour and have red/white elements to match the logo. The red colour used MUST match the red colour used in the logo.
• Please have a go at creating it how you think is best and provide feedback from there. I am leaving it very open to the designers so I can get the best website possible and lots of different ideas etc.

```html
<!DOCTYPE html>
<html lang="en">
<head>
<meta charset="utf-8">
<title>TuneRoost — Live Music Booking</title>
<link href="https://fonts.googleapis.com/css2?family=Questrial&family=Open+Sans:wght@300;400;600&display=swap" rel="stylesheet">
<style>
:root{
  --red:#d1000e;
  --white:#ffffff;
  --ink:#1f1f1f;
  --grey-text:#444444;
  --step-num:#bdbdbd;
  --contact-bg:#333333;
  --footer-bg:#1b1b1b;
  --line:#8a8a8a;
}
*{box-sizing:border-box;margin:0;padding:0}
html,body{width:1200px;height:3429px;overflow:hidden}
body{position:relative;background:var(--white);font-family:"Questrial",sans-serif;color:var(--ink)}
.abs{position:absolute}
section,header,footer{position:absolute;left:0;width:1200px;overflow:hidden}

/* hero */
.hero{top:0;height:766px;color:var(--white)}
.hero-photo{position:absolute;inset:0;
  background:
   radial-gradient(ellipse 420px 260px at 600px 210px,rgba(240,120,200,.75),transparent 70%),
   radial-gradient(ellipse 500px 260px at 620px 470px,rgba(230,90,40,.7),transparent 75%),
   radial-gradient(ellipse 300px 200px at 200px 180px,rgba(150,60,200,.6),transparent 70%),
   radial-gradient(ellipse 300px 200px at 1000px 200px,rgba(130,50,190,.6),transparent 70%),
   linear-gradient(180deg,#3a1f6e 0%,#6a2b7a 30%,#7a2e3a 55%,#2a1210 78%,#0d0705 100%)}
.nav a{position:absolute;top:73px;color:var(--white);text-decoration:none;font-size:16px;letter-spacing:.3px}
.brand{position:absolute;left:0;width:1200px;top:20px;text-align:center}
.brand-dot{display:block;margin:0 auto;width:58px;height:58px;border-radius:50%;border:9px solid var(--white)}
.brand-name{display:block;margin-top:6px;font-size:38px;color:var(--white);line-height:1}
.hero h1{position:absolute;top:258px;width:1200px;text-align:center;font-weight:400;font-size:48px}
.hero .lead{position:absolute;top:330px;width:1200px;text-align:center;font-size:30px;line-height:35px}
.hero .cta-note{position:absolute;top:432px;width:1200px;text-align:center;font-size:24px}
.slide-arrow{position:absolute;top:343px;width:52px;height:52px;border-radius:50%;background:rgba(255,255,255,.35)}
.slide-arrow svg{position:absolute;left:16px;top:16px}

.signup{position:absolute;background:var(--white);display:flex;align-items:center}
.signup .field{flex:1;color:#555;font-family:"Open Sans",sans-serif}
.signup .btn{background:var(--red);color:var(--white);display:flex;align-items:center;justify-content:center}
.signup-lg{left:354px;top:480px;width:497px;height:52px;padding:6px}
.signup-lg .field{font-size:14px;padding-left:16px}
.signup-lg .btn{width:138px;height:41px;font-size:19px}
.signup-sm{width:384px;height:41px;padding:4px}
.signup-sm .field{font-size:11px;padding-left:14px}
.signup-sm .btn{width:107px;height:32px;font-size:14px}

/* how it works */
.how{top:766px;height:487px}
.how h2{position:absolute;top:60px;width:1200px;text-align:center;font-weight:400;font-size:32px;color:#222}
.step-text{position:absolute;width:220px;margin-left:-110px;text-align:center;font-size:17px;line-height:20px;color:#222}
.step-num{position:absolute;width:60px;margin-left:-30px;text-align:center;font-size:42px;color:var(--step-num);top:263px}
.wave{position:absolute;left:0;top:0}

/* why */
.why{top:1253px;height:471px;background:var(--red);color:var(--white)}
.why h2{position:absolute;top:55px;width:1200px;text-align:center;font-weight:400;font-size:33px}
.perk-icon{position:absolute;width:86px;height:86px;border-radius:50%;border:9px solid var(--white)}
.perk-icon svg{position:absolute;left:50%;top:50%;transform:translate(-50%,-50%)}
.perk-title{position:absolute;font-size:26px}
.perk-desc{position:absolute;font-family:"Open Sans",sans-serif;font-size:13px;line-height:22px;width:260px}
.dollar{position:absolute;left:0;right:0;top:50%;transform:translateY(-52%);text-align:center;font-size:40px;font-family:"Open Sans",sans-serif;font-weight:600}

.divider-mark{position:absolute;left:555px;top:1206px;width:74px;height:74px;border-radius:50%;background:var(--white);z-index:3}
.divider-mark span{position:absolute;left:17px;top:17px;width:40px;height:40px;border-radius:50%;border:6px solid var(--red)}

/* audiences */
.audiences{top:1724px;height:544px}
.panel-photo{position:absolute;top:0;height:544px}
.venues-photo{left:0;width:598px;background:radial-gradient(ellipse 300px 200px at 420px 120px,rgba(80,95,120,.55),transparent 70%),linear-gradient(180deg,#1e232b 0%,#15191f 60%,#0e1014 100%)}
.artists-photo{left:598px;width:602px;background:radial-gradient(ellipse 260px 300px at 520px 200px,rgba(150,150,150,.45),transparent 70%),linear-gradient(135deg,#e6e4e3 0%,#d6d3d1 55%,#c9c6c4 100%)}
.audience-title{position:absolute;font-weight:400;font-size:29px}
.perks{position:absolute;list-style:none;font-family:"Open Sans",sans-serif;font-weight:300;font-size:15.5px;line-height:16px}
.perks li{position:absolute;left:0;width:380px;padding-left:16px}
.perks li::before{content:"";position:absolute;left:0;top:4px;width:6px;height:6px;border-right:2px solid currentColor;border-top:2px solid currentColor;transform:rotate(45deg)}
.artists .perks li::before{border-color:var(--red)}
.venues{color:var(--white)}
.artists{color:#333}
.note{position:absolute;left:161px;top:2066px;width:380px;font-family:"Open Sans",sans-serif;font-size:12.5px;line-height:19px;color:#d8d8d8}
.profile-call{position:absolute;left:660px;top:2122px;font-family:"Open Sans",sans-serif;font-size:17.5px;color:#222}

/* about */
.about{top:2268px;height:492px}
.about-photo{position:absolute;left:169px;top:72px;width:354px;height:354px;border-radius:50%;background:radial-gradient(circle at 55% 35%,#4a5866 0%,#262d35 45%,#0f1216 100%)}
.about h2{position:absolute;left:565px;top:83px;font-weight:400;font-size:36px;color:#222}
.about p{position:absolute;left:565px;width:490px;font-family:"Open Sans",sans-serif;font-size:13.5px;line-height:23px;color:var(--grey-text)}
.btn-red{position:absolute;background:var(--red);color:var(--white);display:flex;align-items:center;justify-content:center}

/* contact */
.contact{top:2760px;height:483px;background:var(--contact-bg);color:var(--white)}
.contact h2{position:absolute;left:142px;top:62px;font-weight:400;font-size:35px}
.form-field{position:absolute;left:142px;width:390px;border-bottom:1px solid var(--line);font-family:"Open Sans",sans-serif;font-size:16px;color:#e6e6e6}
.map{position:absolute;left:598px;top:0;width:602px;height:483px;background:linear-gradient(160deg,#dcdcdc 0%,#cfcfcf 50%,#d8d8d8 100%)}
.address-card{position:absolute;left:766px;top:234px;width:281px;height:119px;background:var(--white);text-align:center;font-size:18px;line-height:23px;color:#222;padding-top:33px}
.map-pin{position:absolute;left:890px;top:160px}

/* footer */
.site-footer{top:3243px;height:186px;background:var(--footer-bg);color:var(--white)}
.foot-nav{position:absolute;top:47px;width:1200px;display:flex;justify-content:center;gap:28px;font-size:16px}
.copyright{position:absolute;top:80px;width:1200px;text-align:center;font-size:13px;color:#ddd}
.social{position:absolute;top:125px;width:20px;height:20px;border-radius:50%;border:2px solid var(--white)}
</style>
</head>
<body>

<header class="hero">
  <div class="hero-photo" role="img" aria-label="Concert crowd with raised hands under purple and orange stage lights"></div>
  <nav class="nav">
    <a style="left:134px">ABOUT</a>
    <a style="left:221px">HOW IT WORK</a>
    <a style="left:360px">WHY TUNEROOST</a>
    <a style="left:748px">VENUES</a>
    <a style="left:841px">ARTISTS</a>
    <a style="left:935px">CONTACT US</a>
  </nav>
  <div class="brand"><span class="brand-dot"></span><span class="brand-name">TuneRoost</span></div>
  <div class="slide-arrow" style="left:127px"><svg width="20" height="20" viewBox="0 0 20 20"><path d="M13 2 L5 10 L13 18" fill="none" stroke="#111" stroke-width="2.5"/></svg></div>
  <div class="slide-arrow" style="left:1013px"><svg width="20" height="20" viewBox="0 0 20 20"><path d="M7 2 L15 10 L7 18" fill="none" stroke="#111" stroke-width="2.5"/></svg></div>
  <h1>Zipride for Live Music</h1>
  <p class="lead">TuneRoost connects venues with artists to<br>make booking gigs simple</p>
  <p class="cta-note">Sign up now for FREE</p>
  <div class="signup signup-lg"><span class="field">Email address</span><span class="btn">Click here</span></div>
</header>

<section class="how">
  <h2>How TuneRoost Works</h2>
  <svg class="wave" width="1200" height="487" viewBox="0 0 1200 487">
    <path d="M177,285 C200,260 215,248 237,248 C290,248 310,324 360,324 C420,324 420,248 479,248 C540,248 540,324 597,324 C655,324 655,248 713,248 C775,248 775,324 833,324 C890,324 890,248 947,248 C985,248 1010,290 1036,311" fill="none" stroke="#d1000e" stroke-width="2.5"/>
    <g fill="#fff" stroke="#d1000e" stroke-width="2">
      <circle cx="237" cy="248" r="8"/><circle cx="360" cy="324" r="8"/><circle cx="597" cy="324" r="8"/><circle cx="833" cy="324" r="8"/><circle cx="947" cy="248" r="8"/>
    </g>
  </svg>
  <p class="step-text" style="left:253px;top:163px">Artists and venues<br>sign up for free and<br>create a profile</p>
  <p class="step-text" style="left:369px;top:345px">Venues search for an<br>artist for their<br>upcoming gigs</p>
  <p class="step-text" style="left:588px;top:150px">Venues request a<br>quote and<br>communicate with<br>the artist direct</p>
  <p class="step-text" style="left:839px;top:345px">The gig is booked in<br>once payment is<br>provided by the<br>venue.</p>
  <p class="step-text" style="left:947px;top:131px">Upon completion the<br>money is paid to the<br>artist within 48<br>hours or less.</p>
  <span class="step-num" style="left:235px">1</span>
  <span class="step-num" style="left:360px">2</span>
  <span class="step-num" style="left:592px">3</span>
  <span class="step-num" style="left:829px">4</span>
  <span class="step-num" style="left:947px">5</span>
</section>

<div class="divider-mark"><span></span></div>

<section class="why">
  <h2>Why TuneRoost?</h2>
  <div class="perk-icon" style="left:204px;top:135px"><svg width="40" height="30" viewBox="0 0 40 30"><path d="M3 14 L15 26 L37 3" fill="none" stroke="#fff" stroke-width="3"/></svg></div>
  <p class="perk-title" style="left:311px;top:140px">Simple</p>
  <p class="perk-desc" style="left:311px;top:173px">TuneRoost makes gig booking easy for both the venue and artist.</p>

  <div class="perk-icon" style="left:645px;top:135px"><svg width="30" height="36" viewBox="0 0 30 36"><path d="M8 16 V10 a7 7 0 0 1 14 0 V16" fill="none" stroke="#fff" stroke-width="3"/><rect x="3" y="16" width="24" height="18" fill="none" stroke="#fff" stroke-width="3"/><circle cx="15" cy="24" r="3" fill="#fff"/></svg></div>
  <p class="perk-title" style="left:753px;top:140px">Protection</p>
  <p class="perk-desc" style="left:753px;top:173px;width:260px">Everyone is protected with our complimentary dispute resolutions.</p>

  <div class="perk-icon" style="left:211px;top:286px"><svg width="40" height="40" viewBox="0 0 40 40" fill="none" stroke="#fff" stroke-width="2"><circle cx="20" cy="20" r="4"/><line x1="20" y1="20" x2="6" y2="6"/><line x1="20" y1="20" x2="34" y2="6"/><line x1="20" y1="20" x2="6" y2="34"/><line x1="20" y1="20" x2="34" y2="34"/><line x1="20" y1="20" x2="20" y2="4"/><circle cx="6" cy="6" r="3"/><circle cx="34" cy="6" r="3"/><circle cx="6" cy="34" r="3"/><circle cx="34" cy="34" r="3"/><circle cx="20" cy="4" r="3"/></svg></div>
  <p class="perk-title" style="left:319px;top:292px">Connect</p>
  <p class="perk-desc" style="left:319px;top:324px;width:250px">Join the TuneRoost community which is full of amazing artists and venues.</p>

  <div class="perk-icon" style="left:651px;top:286px"><span class="dollar">$</span></div>
  <p class="perk-title" style="left:760px;top:292px">Price</p>
  <p class="perk-desc" style="left:760px;top:324px;width:270px">Get the best rate possible with TuneRoost only receiving 5% of the artists fee</p>
</section>

<section class="audiences">
  <div class="panel-photo venues-photo" role="img" aria-label="Dimly lit live music venue with audience"></div>
  <div class="panel-photo artists-photo" role="img" aria-label="Musician playing piano, faded light grey photo"></div>
</section>

<div class="venues">
  <h3 class="abs audience-title" style="left:161px;top:1782px">Venues</h3>
  <ul class="perks" style="left:168px;top:1840px">
    <li style="top:0">TuneRoost is a 100% FREE service for all venues - you pay us nothing!</li>
    <li style="top:44px">Get instant access to hundreds of artists around your local community</li>
    <li style="top:87px">All genres to suit any venue from a pub to a wedding or even a nightclub</li>
    <li style="top:130px">Simple booking process with a money back guarantee</li>
    <li style="top:173px">Communicate directly with the artist and negotiate the price</li>
  </ul>
  <p class="note">TuneRoost is not yet ready to host gigs as we're currently working on building our artists. We are launching for venues in Q4 2019. Pre-register now to keep informed and be one of the first people to use our platform.</p>
  <div class="signup signup-sm" style="left:161px;top:2164px"><span class="field">Email address</span><span class="btn">Click here</span></div>
</div>

<div class="artists">
  <h3 class="abs audience-title" style="left:660px;top:1791px">Artists</h3>
  <ul class="perks" style="left:662px;top:1849px">
    <li style="top:0;width:400px">Sign up to TuneRoost for FREE and get yourself in front of venues</li>
    <li style="top:55px;width:400px">Only pay us if you get a gig - we only get 5% of the fee you charge the venue</li>
    <li style="top:108px;width:400px">All genres and artists welcome - as long as you're experienced and professional</li>
    <li style="top:163px;width:400px">Get paid within 48 hours or less after the gig guaranteed!</li>
    <li style="top:216px;width:400px">Negotiate your price and don't pay huge agent fees to ensure you earn top dollar</li>
  </ul>
  <p class="profile-call">Sign up and create your TuneRoost profile now</p>
  <div class="signup signup-sm" style="left:660px;top:2163px"><span class="field">Email address</span><span class="btn">Click here</span></div>
</div>

<section class="about">
  <div class="about-photo" role="img" aria-label="Young musician singing into a microphone while playing acoustic guitar"></div>
  <h2>About TuneRoost</h2>
  <p style="top:145px">Ast nunc venenatis in tristique eu imperdiet ac nisl Cum sociis natoque penatibus et magnis dis parturient montes nascetur ridiculus</p>
  <p style="top:216px">Aeo molestie sed luctus quis feugiat in pede Fusce tellus Sed metus augue convallis et vehicula ut pulvinar eu ante Integer orci tellus tristique vitae consequat nec porta vel lectus Nulla sit amet diam enim Proin dui lectus cursus eu mattis laoreet viverra sit amet quam Curabitur vel dolor ultrices ipsum dictum tristique Praesent vitae lacus Ut</p>
  <span class="btn-red" style="left:565px;top:356px;width:153px;height:43px;font-size:17px">Learn More</span>
</section>

<section class="contact">
  <h2>Contact Us</h2>
  <div class="form-field" style="top:120px;height:30px">Name *</div>
  <div class="form-field" style="top:164px;height:30px">Company</div>
  <div class="form-field" style="top:214px;height:29px">E-mail *</div>
  <div class="form-field" style="top:260px;height:30px">Phone Number *</div>
  <div class="form-field" style="top:303px;height:56px">Message</div>
  <span class="btn-red" style="left:146px;top:379px;width:153px;height:43px;font-size:19px">Submit</span>
  <div class="map" role="img" aria-label="Street map around the office location"></div>
  <svg class="map-pin" width="34" height="44" viewBox="0 0 34 44"><path d="M17 43 C17 43 2 24 2 16 a15 15 0 0 1 30 0 C32 24 17 43 17 43 Z" fill="#d1000e"/><circle cx="17" cy="16" r="6" fill="#fff"/></svg>
  <div class="address-card">48 Harmon Lane Suite 4B<br>Austin 73301 TX<br>512.555.0186</div>
</section>

<footer class="site-footer">
  <nav class="foot-nav"><span>ABOUT US</span><span>HOW IT WORK</span><span>WHY TUNEROOST</span><span>VENUES</span><span>ARTISTS</span><span>CONTACT US</span></nav>
  <p class="copyright">© 2019 Company Name &nbsp;All right reserved</p>
  <span class="social" style="left:505px"></span>
  <span class="social" style="left:560px"></span>
  <span class="social" style="left:614px"></span>
  <span class="social" style="left:670px"></span>
</footer>

</body>
</html>
```